IT Company needs Website for new Web and Mobile products for Sports and Fitness

Background:

We developed web based white label frontend web solution, backend services and white label mobile apps for to log, analyze, share and control sport and fitness activities. The name of this product suite is "Trevantix" (http://trevantix-example.com)

This products will be used by customers that provide platforms and community systems for sport and fitness. One of the major USP's is, that our technology i open for nearly all common formats, devices and apps out in the market. This means, you can just upload your data directly from device, file or app - e.G. Kestrel, Bolvane, Ravelo, StrideVault, Pacelumo, Zembra and much others.

Two current concrete examples/References

(1) MyQuorel
It's an international platform from quorel for runners. It provides individual training lans and a training log. MyQuorel uses the Backend Product "Trevantix Hub" (see http://hub.trevantix-example.net for a landing page) to integrate device, file and app support. Before this, every user has to track his training with manual inputs

(2) Paceharbor and fen-zine
Both are German customers. Paceharor is focused on runners. fen-zine is focused on Triatheletes. Both use the Product "Trevantix Web". This is a complete web solution with web based frontend solutions for athletes and coaches.

What do we need?
We need website layout for B2B for our products. We don't need lot's of pages. We need the pretty and nice layout, so we can derive the pages we need.

IMPORTANT
We don't talk about the webpages for the product itself (this will be a different project in future). We talk about a website, explaining the products)
Updates

Hi all,

we just start reviewing the first designs, and try to give feedback as detailed as possible. We attached a PDF document, to describe the the products a little bit more detailed. 

As written in the description, in the end we have two different sections. One is the usual stuff like "start page", "about", "contact", "disclaimer", "pricing", "blah...." and one will be the Developer Section, the "Tec Section". This ist aimed to developers (of our customers) that will integrate our products in there existing system or which will integrate our services in there own software.  This "pages" are more like "documentation", so easy to read and cool to look at (cause developers likes it cool, but straight)

Dear all,

we just do the final review. Cause this week is with heavy load, it takes some time...

Cheers

Odell

Target Market(s)

* Platforms and Communities for sport, health and fitness
* Gyms

Industry/Entity Type

Concrete

Font styles to use
Sans Serif

Requirements
Must have
• * Templates shall base on bootstrap. If not, it shall be easily realized on our site with bootstrap or out of the box "full responsive"

* HTML5 / CSS3
Nice to have
• PAGES
- Start Page
- Generic Template (from which we can derive additional pages)
- Contact Page
- Disclaimer Page
- Blog/News Page
- "About us" Page (can be combined with disclaimer)
- One Example product page (in end we have 3 products), shall show (if you need product details, let me know)
- product and it's description
- pricing information
- Add-Ons for the product
- Developer Section Page (Start Point for developers, where the finde "basic technical concepts and developer API's
- Example Developer Page for technical concept
- Example Developer Page for API

LOGO ISSUE
You can use an align to the Logo attached OR provide a new logo. The given logo is a logo for our own B2C Website http://trevantix-example.net. It's not really necessary, that the logo or the color must be used for the product website. Maybe it will be better if it's a complete new one, to avoid irritation between Trevantix as a B2B product and trevantix-example.net as a B2C platform.
Should not have
• No Flash and other proprietary technologies

```html
<!DOCTYPE html>
<html lang="en">
<head>
<meta charset="utf-8">
<title>Trevantix – Digital Sport and Fitness Services</title>
<link rel="stylesheet" href="https://fonts.googleapis.com/css2?family=Source+Sans+3:ital,wght@0,400;0,600;0,700;1,400&family=Roboto+Condensed:wght@500&display=swap">
<style>
:root{
  --orange:#e8821c;
  --orange-dark:#d06a0c;
  --ink:#3a3a3a;
  --text:#444;
  --muted:#888;
  --rule:#d9d9d9;
  --news-date:#c8102e;
  --footer:#4a4a4a;
  --footer-text:#c9c9c9;
  --social:#6f7f99;
}
*{margin:0;padding:0;box-sizing:border-box}
html,body{width:1171px;height:1200px;overflow:hidden;background:#fff}
body{font-family:"Source Sans 3",Arial,sans-serif;color:var(--text)}
.page{position:relative;width:1400px;height:1435px;transform:scale(.836429);transform-origin:0 0}
.abs{position:absolute}

/* header */
.brand{left:212px;top:14px}
.brand-name{font-size:44px;font-weight:700;color:var(--orange);line-height:1;letter-spacing:.5px}
.brand-tag{font-size:9px;font-weight:700;color:#222;margin-top:18px;letter-spacing:.2px}
.main-nav{left:480px;top:40px;display:flex;height:28px;align-items:center}
.main-nav a{font-size:12px;color:#555;text-decoration:none;text-transform:uppercase;padding:0 35px;border-left:1px solid var(--rule);line-height:28px}
.main-nav a:first-child{border-left:none;padding-left:27px}
.main-nav a:last-child{padding-right:0}

/* hero */
.hero{left:0;top:106px;width:1400px;height:495px}
.hero-photo{position:absolute;inset:0;background:
  radial-gradient(ellipse at 15% 35%,#fbe6b0 0%,rgba(248,205,130,.6) 30%,transparent 60%),
  radial-gradient(ellipse at 82% 70%,#d8433a 0%,rgba(200,80,50,.5) 22%,transparent 45%),
  linear-gradient(90deg,#f6d08c 0%,#eab066 40%,#c97a45 70%,#8d4e34 100%)}
.hero-arrow{position:absolute;top:210px;width:50px;height:50px}
.hero-title{position:absolute;left:211px;top:138px;font-family:"Roboto Condensed",Arial,sans-serif;font-weight:500;font-size:38px;line-height:47px;text-transform:uppercase}
.hero-title .accent{color:var(--orange)}
.hero-title .dark{color:var(--ink)}
.signup{position:absolute;left:210px;top:251px;width:447px;height:47px;background:#fff;border:1px solid #cfcfcf;border-radius:3px}
.signup-field{position:absolute;left:18px;top:16px;font-size:12px;color:var(--muted)}
.signup-btn{position:absolute;right:2px;top:2px;width:155px;height:41px;border-radius:3px;background:linear-gradient(#f3a73a,var(--orange-dark));color:#fff;font-size:18px;text-align:center;line-height:41px}
.hero-dot{position:absolute;left:1142px;top:470px;width:12px;height:12px;border-radius:50%;background:#e8e3de}

/* intro */
.devices{left:210px;top:640px;width:302px;height:188px;background:linear-gradient(180deg,#ececec,#cfcfcf);border-radius:6px}
.h-section{font-size:20px;color:var(--orange);text-transform:uppercase;font-weight:400}
.welcome{left:549px;top:636px;width:310px}
.welcome p{font-size:11px;line-height:18px;color:var(--text);margin-top:10px}
.store-badge{top:776px;width:144px;height:49px;background:#111;border-radius:5px;border:1px solid #555}
.vrule{left:893px;top:640px;width:1px;height:188px;background:var(--rule)}
.news{left:931px;top:636px;width:259px}
.pager{display:flex;gap:6px}
.news-item{position:absolute;left:0;width:259px;display:flex;gap:10px}
.news-thumb{width:50px;height:46px;flex:none;background:linear-gradient(135deg,#9fb6cc,#3f5f82);border:1px solid #ccc}
.news-text{font-size:11px;line-height:18px;color:var(--text);text-transform:uppercase}
.news-date{font-size:11px;font-style:italic;color:var(--news-date);text-transform:none}
.news-sep{position:absolute;left:0;top:103px;width:259px;height:1px;background:var(--rule)}

.hrule{left:210px;width:980px;height:1px;background:var(--rule)}

/* services */
.services-title{left:210px;top:888px}
.service{top:932px;width:233px}
.service-photo{width:233px;height:166px;position:relative}
.service-cta{position:absolute;left:0;top:116px;width:190px;height:31px;background:#fff;color:var(--orange);font-size:13px;line-height:31px;padding-left:13px}
.service h3{font-size:13px;font-weight:400;color:var(--orange);text-transform:uppercase;line-height:22px;margin-top:14px}
.service p{font-size:11px;line-height:22px;color:var(--text);margin-top:2px}

/* partners */
.partners{left:210px;top:1250px;width:980px;height:66px;display:flex;justify-content:space-around;align-items:center}
.partner{font-size:30px;font-weight:700;color:#333;letter-spacing:1px}

/* footer */
.footer{left:0;top:1337px;width:1400px;height:98px;background:var(--footer)}
.footer-nav{position:absolute;left:213px;top:28px;display:flex;font-size:10px;color:var(--footer-text);text-transform:uppercase}
.footer-nav span{padding:0 18px;border-left:1px solid var(--footer-text);line-height:11px}
.footer-nav span:first-child{border:none;padding-left:0}
.copyright{position:absolute;left:213px;top:58px;font-size:10px;color:var(--footer-text)}
.follow{position:absolute;left:1012px;top:35px;display:flex;align-items:center;gap:6px;font-size:9px;color:var(--footer-text)}
.follow i{display:block;width:23px;height:23px;border-radius:50%;background:var(--social)}
</style>
</head>
<body>
<div class="page">

  <header>
    <div class="abs brand">
      <div class="brand-name">Trevantix</div>
      <div class="brand-tag">DIGITAL SPORT AND FITNESS SERVICES</div>
    </div>
    <nav class="abs main-nav">
      <a href="#">Home</a><a href="#">Trevantix</a><a href="#">Fitness Cloud</a><a href="#">References</a><a href="#">Products</a><a href="#">Services</a>
    </nav>
  </header>

  <section class="abs hero">
    <div class="hero-photo" role="img" aria-label="Runner's red running shoes on a track in warm sunset light"></div>
    <svg class="hero-arrow" style="left:101px" viewBox="0 0 50 50"><circle cx="25" cy="25" r="23" fill="none" stroke="rgba(255,255,255,.75)" stroke-width="2"/><path d="M30 14 L17 25 L30 36 Z" fill="rgba(255,255,255,.75)"/></svg>
    <svg class="hero-arrow" style="left:1261px" viewBox="0 0 50 50"><circle cx="25" cy="25" r="23" fill="none" stroke="rgba(255,255,255,.75)" stroke-width="2"/><path d="M20 14 L33 25 L20 36 Z" fill="rgba(255,255,255,.75)"/></svg>
    <h1 class="hero-title"><span class="accent">Die offene Sport- und</span><br><span class="dark">Fitnessplatform fur jeden Sport</span></h1>
    <div class="signup">
      <span class="signup-field">WHAT'S YOUR EMAIL ADDRESS :</span>
      <span class="signup-btn">JOIN FOR FREE</span>
    </div>
    <span class="hero-dot"></span>
  </section>

  <div class="abs devices" role="img" aria-label="Trevantix shown on desktop, tablet and phone screens"></div>

  <section class="abs welcome">
    <h2 class="h-section">Welcome to Trevantix</h2>
    <p>Mit trevantix-example.net kannst du deinen Sport festhalten, auswerten, teilen, dich motivieren und coachen lassen. Nutze einfach deine Lieblings-App, deinen bevorzugten Sportcomputer oder trage manuell ein. Trevantix begleitet, fördert und motiviert dich dein gesamtes Sportlerleben.</p>
  </section>
  <div class="abs store-badge" style="left:550px"></div>
  <div class="abs store-badge" style="left:710px"></div>

  <div class="abs vrule"></div>

  <section class="abs news" style="height:180px">
    <h2 class="h-section">Latest News</h2>
    <svg class="abs" style="left:232px;top:3px" width="27" height="12" viewBox="0 0 27 12"><path d="M7 1 L2 6 L7 11" fill="none" stroke="#999" stroke-width="2"/><path d="M20 1 L25 6 L20 11" fill="none" stroke="#999" stroke-width="2"/></svg>
    <div class="news-item" style="top:39px">
      <div class="news-thumb" role="img" aria-label="Runner silhouette"></div>
      <div class="news-text">The only good race pace is a suicide pace, and today looks like...<br><span class="news-date">11/1/2013 - 7:38:00 PM</span></div>
    </div>
    <div class="news-sep"></div>
    <div class="news-item" style="top:123px">
      <div class="news-thumb" role="img" aria-label="Sprinters crossing a finish line"></div>
      <div class="news-text">The only good race pace is a suicide pace, and today looks like...<br><span class="news-date">11/1/2013 - 7:38:00 PM</span></div>
    </div>
  </section>

  <div class="abs hrule" style="top:863px"></div>

  <h2 class="abs h-section services-title">Services</h2>
  <svg class="abs" style="left:1163px;top:900px" width="27" height="12" viewBox="0 0 27 12"><path d="M7 1 L2 6 L7 11" fill="none" stroke="#999" stroke-width="2"/><path d="M20 1 L25 6 L20 11" fill="none" stroke="#999" stroke-width="2"/></svg>

  <article class="abs service" style="left:210px">
    <div class="service-photo" role="img" aria-label="Sprinter pushing off from the start in a dust cloud" style="background:linear-gradient(135deg,#3e3a36,#b8ada2 55%,#5a5148)"><span class="service-cta">CLICK HERE FOR MORE INFO</span></div>
    <h3>Custom development for device vendors</h3>
    <p>Convert data from several formats and provide in one format via normalized JSON format</p>
  </article>
  <article class="abs service" style="left:459px">
    <div class="service-photo" role="img" aria-label="Close-up of runners in starting blocks on a red track" style="background:linear-gradient(135deg,#b2473a,#d9a28a 45%,#8a2f2a)"><span class="service-cta">CLICK HERE FOR MORE INFO</span></div>
    <h3>Integration development for trevantix customers / distributions</h3>
    <p>Convert data from several formats and provide in one format via normalized JSON format</p>
  </article>
  <article class="abs service" style="left:708px">
    <div class="service-photo" role="img" aria-label="Athlete sprinting in an empty stadium at dusk" style="background:linear-gradient(180deg,#2c2c2e,#55565a 60%,#3b3b3d)"><span class="service-cta">CLICK HERE FOR MORE INFO</span></div>
    <h3 style="margin-left:5px">1st level support</h3>
    <p style="margin-left:5px">Convert data from several formats and provide in one format via normalized JSON format</p>
  </article>
  <article class="abs service" style="left:957px">
    <div class="service-photo" role="img" aria-label="Woman running in blue training gear against a grey wall" style="background:linear-gradient(135deg,#c9c9c9,#a6a6a6 60%,#8e8e8e)"><span class="service-cta">CLICK HERE FOR MORE INFO</span></div>
    <h3 style="margin-left:6px">Data andstore management &amp; operations</h3>
    <p style="margin-left:6px">Convert data from several formats and provide in one format via normalized JSON format</p>
  </article>

  <div class="abs hrule" style="top:1233px"></div>

  <div class="abs partners">
    <span class="partner">KESTREL</span>
    <span class="partner">BOLVANE</span>
    <span class="partner">Halvero</span>
    <span class="partner">NORQUIST</span>
    <span class="partner">Lumbrix</span>
    <span class="partner">Quillo</span>
  </div>

  <footer class="abs footer">
    <div class="footer-nav"><span>Home</span><span>About Trevantix</span><span>Press</span><span>Blog</span><span>Support</span><span>Imprint</span></div>
    <div class="copyright">COPYRIGHTS© 2013. TREVANTIX. ALL RIGHTS RESERVED.</div>
    <div class="follow">FOLLOW US : <i></i><i></i><i></i><i></i></div>
  </footer>

</div>
</body>
</html>
```